Ecommerce site that acts also as a portal for B2C members and non- members and B2B. Please see attachment this is for only front end work, backend will follow. Husk and Kettle- a MRVL Hospitality Company

Products
Coffee bean sourcing, acquisition, roasting, grinding, blending, sale/delivery
Tea sourcing, acquisition, roasting, grinding, blending, sale/delivery
Applicable/Associated Merchandise and Accoutrements

Initial market penetration for both B2C and B2B offering Husk and Kettle custom blends of both Coffees and Teas.
B2C- Zelvora style sale/distribution via guest and members. Members initial fee $129 annual $99 a year thereafter with benefits such as 1st year gift of a French Press Travel Mug (customized/logo/name/brand), monthly samples. Attached document has non project related information for narrative and conceptual inputs.

Coding

```html
<!DOCTYPE html>
<html lang="en">
<head>
<meta charset="utf-8">
<title>Husk and Kettle — Luxury Coffee &amp; Tea</title>
<link href="https://fonts.googleapis.com/css2?family=Roboto:ital,wght@0,400;0,500;0,700;0,900;1,400&family=Cormorant+Garamond:wght@500;600&display=swap" rel="stylesheet">
<style>
:root{
  --espresso:#3b2118;
  --espresso-deep:#2a170f;
  --rust:#a0553a;
  --rust-dark:#8a4530;
  --cream:#efece6;
  --card-label:#ebe6dd;
  --white:#ffffff;
  --text:#3a3330;
  --muted:#5d5550;
  --star:#e8832a;
  --brand-ink:#eadfd2;
}
*{box-sizing:border-box;margin:0;padding:0}
html,body{width:1200px;height:4677px;overflow:hidden}
body{font-family:"Roboto",sans-serif;color:var(--text);background:var(--cream);position:relative}
.abs{position:absolute}
.btn{position:absolute;display:flex;align-items:center;justify-content:center;border-radius:20px;font-size:12px;font-weight:700;letter-spacing:.3px;text-transform:uppercase}
.btn-rust{background:var(--rust);color:var(--white)}
.btn-light{background:var(--white);color:var(--espresso)}
.btn-dark{background:var(--espresso);color:var(--white)}
.rule{position:absolute;height:3px;width:80px;background:var(--rust);left:560px}
.section-title{position:absolute;left:0;width:1200px;text-align:center;font-weight:500;color:var(--espresso);font-size:40px}

/* brand name */
.brand{position:absolute;display:flex;align-items:center;gap:8px;font-family:"Roboto",sans-serif;font-weight:500;color:var(--brand-ink);white-space:nowrap}
.brand .mark{border-radius:50%;background:var(--brand-ink);flex:none}

/* header */
.nav{position:absolute;left:380px;top:0;width:720px;height:80px;background:var(--white);border-radius:0 0 14px 14px;display:flex;align-items:center}
.nav a{font-size:15px;font-weight:500;color:#1c1c1c;text-decoration:none;margin-right:29px}
.nav .active{background:var(--espresso);color:var(--white);height:80px;padding:0 12px;display:flex;align-items:center;margin-right:22px}
.nav .quote{margin-left:24px;width:148px;height:38px;position:relative}

/* hero */
.hero{position:absolute;left:0;top:0;width:1200px;height:720px;background:radial-gradient(circle at 28% 55%,#6b4a36 0,#3a2419 35%,#1f120c 75%)}
.hero-photo{position:absolute;left:0;top:0;width:1200px;height:720px}
.hero h1{position:absolute;left:575px;top:168px;font-size:57px;line-height:57px;font-weight:700;color:var(--white);letter-spacing:.3px}
.hero .sub{position:absolute;left:580px;top:296px;font-size:31px;color:var(--white)}
.circle-arrow{position:absolute;width:48px;height:48px;border-radius:50%;background:var(--white);display:flex;align-items:center;justify-content:center}

/* about */
.about{position:absolute;left:0;top:720px;width:1200px;height:560px}
.ph{position:absolute}
.about h2{position:absolute;left:627px;top:86px;font-size:43px;font-weight:700;color:var(--espresso)}
.about p{position:absolute;left:628px;top:165px;width:426px;font-size:13.5px;line-height:24px;text-align:justify;color:var(--muted)}

/* featured */
.featured{position:absolute;left:0;top:1280px;width:1200px;height:600px;background:var(--white)}
.featured .lead{position:absolute;left:290px;top:170px;width:620px;text-align:center;font-size:13.5px;line-height:24px;color:var(--text)}
.card{position:absolute;top:237px;width:211px;height:290px;background:var(--white);border-radius:26px;box-shadow:0 4px 14px rgba(60,30,20,.16)}
.card .img{position:absolute;left:20px;top:22px;width:171px;height:168px;border-radius:16px}
.card .label{position:absolute;left:9px;right:9px;bottom:9px;height:80px;background:var(--card-label);border-radius:0 0 20px 20px;text-align:center;padding-top:18px;font-size:15px;font-weight:500;color:#1f1f1f}
.card .label .price{display:block;margin-top:8px;font-size:16px}
.card.selected .label{background:var(--rust);color:var(--white);border-radius:10px 10px 20px 20px}
.badge{position:absolute;right:14px;top:18px;width:52px;height:52px;border-radius:50%;border:2px solid #c9a56e}
.side-arrow{position:absolute;top:1630px}

/* subscription */
.beans-band{position:absolute;left:0;top:1868px;width:1200px;height:168px}
.subscription{position:absolute;left:0;top:2033px;width:1200px;height:632px;background:linear-gradient(180deg,#e6e4df,#eeede9 50%,#e4e2dd)}
.step{position:absolute;top:172px;width:200px;height:255px;background:var(--white);border-radius:26px 18px 30px 16px;text-align:center}
.step .ring{position:absolute;left:37px;top:30px;width:126px;height:126px;border-radius:50%;border:3px dotted var(--espresso)}
.step .icon{position:absolute;left:46px;top:39px;width:108px;height:108px;border-radius:50%;background:var(--rust);display:flex;align-items:center;justify-content:center}
.step .num{position:absolute;left:116px;top:18px;width:34px;height:34px;border-radius:50%;background:var(--espresso);color:var(--white);font-size:14px;font-weight:700;display:flex;align-items:center;justify-content:center;border:3px solid var(--white)}
.step .name{position:absolute;left:0;width:200px;top:168px;font-size:18px;font-weight:500;line-height:27px;color:#1f1f1f}
.subscription .note{position:absolute;left:0;width:1200px;top:444px;text-align:center;font-size:16px;line-height:28px;color:#2b2b2b}

/* wholesale */
.wholesale{position:absolute;left:0;top:2665px;width:1200px;height:360px;background:radial-gradient(ellipse at 55% 70%,#b8694a 0,#a65637 40%,#8d4329 100%)}
.wholesale h2{position:absolute;left:0;width:1200px;top:90px;text-align:center;color:var(--white);font-size:36px;font-weight:500;line-height:44px}

/* membership */
.membership{position:absolute;left:0;top:3025px;width:1200px;height:580px}
.membership h2{position:absolute;left:142px;top:106px;font-size:40px;line-height:48px;font-weight:700;color:var(--espresso)}
.membership .subhead{position:absolute;left:142px;top:225px;font-family:"Cormorant Garamond",serif;font-size:24px;font-weight:500;color:#2b2b2b}
.benefits{position:absolute;left:142px;top:270px;list-style:none}
.benefits li{font-size:15px;line-height:32px;color:#3b3b3b;display:flex;align-items:center}
.benefits li svg{margin-right:10px}
.membership .price{position:absolute;left:142px;top:413px;font-size:23px;font-weight:700;color:var(--espresso)}

/* testimonials */
.quote-card{position:absolute;width:286px;height:224px;background:var(--white);border-radius:18px;box-shadow:0 5px 0 var(--espresso),0 6px 14px rgba(0,0,0,.12);text-align:center;padding:26px 28px 0}
.quote-card .stars{color:var(--star);font-size:16px;letter-spacing:2px}
.quote-card p{font-size:13.5px;font-style:italic;line-height:20px;color:#333;margin-top:8px}
.quote-card hr{border:0;border-top:1px solid #ddd;margin:12px 0 8px}
.quote-card .who{font-size:15px;font-weight:700;color:#1f1f1f}
.quote-card .co{font-size:11px;color:#777}
.dots{position:absolute;top:4020px;left:563px;display:flex;gap:8px}
.dots span{width:11px;height:11px;border-radius:50%;background:#cfcac3}
.dots .on{background:var(--espresso)}

/* footer */
.footer{position:absolute;left:0;top:4110px;width:1200px;height:567px}
.footer h4{position:absolute;top:242px;font-size:19px;font-weight:500;color:var(--white);letter-spacing:.5px}
.links{position:absolute;left:392px;top:280px;list-style:none}
.links li{font-size:14px;line-height:24px;color:#f0e6df;display:flex;align-items:center}
.links li::before{content:"";width:8px;height:8px;border-radius:50%;background:var(--rust);margin-right:16px}
.contact-item{position:absolute;left:585px;font-size:14px;line-height:22px;color:#f0e6df}
.contact-item b{font-weight:700;display:block}
.contact-item svg{position:absolute;left:0;top:3px}
.contact-item div{padding-left:24px}
.email-field{position:absolute;left:813px;top:275px;width:245px;height:36px;border-radius:18px;background:#55362a;color:#f0e6df;font-size:14px;display:flex;align-items:center;padding-left:16px}
.email-field svg{margin-right:10px}
.social{position:absolute;top:404px;width:36px;height:36px;border-radius:50%;border:2px solid var(--white)}
.copyright{position:absolute;left:0;width:1200px;top:4635px;text-align:center;color:#f0e6df;font-size:13.5px}
</style>
</head>
<body>

<!-- HERO -->
<section class="hero">
  <div class="hero-photo" role="img" aria-label="Steaming cup of coffee on a saucer with roasted beans on burlap, against a dark background"
       style="background:radial-gradient(ellipse 420px 260px at 230px 420px,rgba(190,170,150,.45),transparent 70%),radial-gradient(ellipse 500px 220px at 500px 560px,rgba(90,50,28,.8),transparent 70%)"></div>
  <h1>Luxury Coffee &amp; Tea.<br>Crafted Your Way.</h1>
  <div class="sub">Source. Roast. Blend. Delivered.</div>
  <div class="btn btn-rust" style="left:577px;top:354px;width:165px;height:36px">Shop Our Coffee</div>
  <div class="btn btn-light" style="left:762px;top:354px;width:182px;height:36px">Build Your Blend</div>
  <div class="circle-arrow" style="left:951px;top:470px">
    <svg width="12" height="12" viewBox="0 0 12 12"><path d="M8 2 4 6l4 4" stroke="#222" stroke-width="1.8" fill="none"/></svg>
  </div>
  <div class="circle-arrow" style="left:1007px;top:470px">
    <svg width="12" height="12" viewBox="0 0 12 12"><path d="M4 2l4 4-4 4" stroke="#222" stroke-width="1.8" fill="none"/></svg>
  </div>
  <svg class="abs" style="left:0;top:480px" width="1200" height="240" viewBox="0 0 1200 240">
    <path d="M0 112 C120 104 200 130 300 110 C390 92 420 40 520 42 C620 44 660 120 760 150 C860 180 920 90 1000 80 C1080 70 1130 140 1200 208 L1200 240 L0 240Z" fill="var(--rust)"/>
    <path d="M0 124 C120 116 200 142 300 122 C390 104 420 58 520 60 C620 62 660 138 760 168 C860 198 920 110 1000 100 C1080 92 1130 160 1200 226 L1200 240 L0 240Z" fill="var(--cream)"/>
  </svg>
</section>

<!-- HEADER -->
<div class="brand" style="left:120px;top:32px;font-size:17px">
  <span class="mark" style="width:14px;height:14px"></span>Husk and Kettle
</div>
<nav class="nav">
  <a class="active">Home</a>
  <a>About</a>
  <a>Products</a>
  <a>Subscription</a>
  <a>Blog</a>
  <a>Contact</a>
  <span class="btn btn-rust quote">Get a Quote</span>
</nav>

<!-- ABOUT -->
<section class="about">
  <div class="ph" role="img" aria-label="Scattered roasted coffee beans" style="left:0;top:88px;width:104px;height:230px;background:radial-gradient(ellipse at 40% 50%,rgba(80,40,20,.55),transparent 70%)"></div>
  <div class="ph" role="img" aria-label="Barista pouring latte art into a cup" style="left:143px;top:70px;width:232px;height:232px;border-radius:26px;background:linear-gradient(140deg,#5a3a28,#a9764f 55%,#3a2418)"></div>
  <div class="ph" style="left:390px;top:100px;width:182px;height:182px;border-radius:50%;border:3px solid var(--rust)"></div>
  <div class="ph" role="img" aria-label="Top view of an espresso cup on a saucer" style="left:398px;top:108px;width:166px;height:166px;border-radius:50%;background:radial-gradient(circle at 45% 45%,#f3f1ee,#c9ccd0 70%,#9aa0a7)"></div>
  <div class="ph" style="left:224px;top:318px;width:134px;height:134px;border-radius:50%;border:3px solid var(--rust)"></div>
  <div class="ph" role="img" aria-label="Cup of green tea with leaves" style="left:231px;top:325px;width:120px;height:120px;border-radius:50%;background:radial-gradient(circle,#7c8a48,#3b3a22 65%,#2a2218)"></div>
  <div class="ph" role="img" aria-label="Couple enjoying coffee together at a cafe" style="left:383px;top:290px;width:190px;height:190px;border-radius:22px;background:linear-gradient(160deg,#b5704a,#d7b08a 50%,#7a4a33)"></div>
  <h2>ABOUT US</h2>
  <div class="rule" style="left:628px;top:146px"></div>
  <p>Lorem ipsum dolor sit amet, consectetur adipiscing elit, sed do eiusmod tempor incididunt ut labore et dolore magna aliqua. Ut enim ad minim veniam, quis nostrud exercitation ullamco laboris nisi ut aliquip ex ea commodo consequat. Duis aute irure dolor in reprehenderit in voluptate velit esse cillum dolore eu fugiat nulla pariatur. Excepteur sint oc=caecat cupidatat non proident, sunt in culpa qui officia deserunt mollit anim id est laborum. Lorem ipsum dolor sit amet, consectetur adipiscing elit, sed do eiusmod tempor incididunt ut labore et dolore magna aliqua. Lorem ipsum dolor sit amet, consectetur adipiscing elit, sed do eiusmod tempor incididunt ut labore et dolore magna aliqua.</p>
  <div class="btn btn-rust" style="left:627px;top:447px;width:148px;height:38px">Learn More</div>
</section>

<!-- FEATURED -->
<section class="featured">
  <div class="section-title" style="top:70px">Featured Coffees</div>
  <div class="rule" style="top:145px"></div>
  <div class="lead">Lorem ipsum dolor sit amet, consectetur adipiscing elit, sed do eiusmod tempor incididunt ut labore et dolore magna aliqua.</div>

  <div class="card" style="left:143px">
    <div class="img" role="img" aria-label="Pile of roasted single-origin coffee beans" style="background:linear-gradient(180deg,#f6f2ec 0%,#d9c2a8 45%,#8a5a3a 100%)"></div>
    <div class="label">Single-Origin Coffees<span class="price">$25.00</span></div>
  </div>
  <div class="card selected" style="left:377px">
    <div class="img" role="img" aria-label="Ground coffee heaped with whole beans" style="background:linear-gradient(180deg,#f6f2ec 0%,#d6b9a0 45%,#7a4a2e 100%)"></div>
    <div class="badge" style="background:#3f4a2a" role="img" aria-label="Single origin badge"></div>
    <div class="label">Custom Coffee Blends<span class="price">$25.00</span></div>
  </div>
  <div class="card" style="left:611px">
    <div class="img" role="img" aria-label="Heap of loose-leaf artisan tea with dried flowers" style="background:linear-gradient(180deg,#f6f2ec 0%,#cfc6c4 45%,#5e5548 100%)"></div>
    <div class="label">Artisan Teas<span class="price">$25.00</span></div>
  </div>
  <div class="card" style="left:845px">
    <div class="img" role="img" aria-label="Kraft paper coffee bag with beans at its base" style="background:linear-gradient(180deg,#f6f2ec 0%,#e0c6a0 45%,#a77a48 100%)"></div>
    <div class="badge" style="background:#6b3a22" role="img" aria-label="Signature blend badge"></div>
    <div class="label">Member Exclusives<span class="price">$25.00</span></div>
  </div>
</section>
<svg class="side-arrow" style="left:64px" width="18" height="28" viewBox="0 0 18 28"><path d="M14 3 4 14l10 11" stroke="#222" stroke-width="2.5" fill="none"/></svg>
<svg class="side-arrow" style="left:1118px" width="18" height="28" viewBox="0 0 18 28"><path d="M4 3l10 11-10 11" stroke="#222" stroke-width="2.5" fill="none"/></svg>

<!-- SUBSCRIPTION -->
<section class="subscription">
  <div class="section-title" style="top:68px">The Subscription Journey</div>
  <div class="rule" style="top:134px"></div>

  <div class="step" style="left:194px">
    <div class="ring"></div>
    <div class="icon"><svg width="56" height="56" viewBox="0 0 56 56" fill="none" stroke="#fff" stroke-width="2.4"><ellipse cx="22" cy="32" rx="12" ry="16" transform="rotate(30 22 32)"/><path d="M14 44c8-6 10-16 16-24"/><ellipse cx="36" cy="22" rx="10" ry="13" transform="rotate(30 36 22)"/><path d="M30 32c5-4 7-12 12-18"/></svg></div>
    <div class="num">01</div>
    <div class="name">Pick Your<br>Favorite Roast</div>
  </div>
  <div class="step" style="left:499px">
    <div class="ring"></div>
    <div class="icon"><svg width="60" height="56" viewBox="0 0 60 56" fill="none" stroke="#fff" stroke-width="2.4"><circle cx="18" cy="16" r="10"/><path d="M18 10v6l4 3"/><path d="M10 30h26v14H10z"/><path d="M36 34h10l6 6v4H36"/><circle cx="18" cy="46" r="4"/><circle cx="44" cy="46" r="4"/></svg></div>
    <div class="num">02</div>
    <div class="name">Choose Your<br>Delivery Schedule</div>
  </div>
  <div class="step" style="left:804px">
    <div class="ring"></div>
    <div class="icon"><svg width="56" height="56" viewBox="0 0 56 56" fill="none" stroke="#fff" stroke-width="2.4"><ellipse cx="20" cy="26" rx="11" ry="15" transform="rotate(-30 20 26)"/><path d="M12 16c6 6 10 14 16 20"/><ellipse cx="36" cy="32" rx="11" ry="15" transform="rotate(-30 36 32)"/><path d="M28 22c6 6 10 14 16 20"/></svg></div>
    <div class="num">03</div>
    <div class="name">Enjoy Fresh<br>Coffee On Autopilot</div>
  </div>

  <div class="note">Our subscription is for people who know what they love. It’s flexible, reliable, and always fresh.<br>Just like our beans.</div>
  <div class="btn btn-dark" style="left:474px;top:504px;width:252px;height:38px">Customize My Subscription</div>
</section>
<div class="beans-band" role="img" aria-label="Band of roasted coffee beans" style="background:linear-gradient(180deg,transparent 0,#4a2a1a 30%,#2e1a10 70%,#3c2418 100%)"></div>

<!-- WHOLESALE -->
<section class="wholesale" aria-label="Wholesale">
  <div class="abs" role="img" aria-label="Blurred coffee cup on a café table, tinted in rust" style="left:0;top:0;width:1200px;height:360px;background:radial-gradient(ellipse 260px 140px at 330px 230px,rgba(255,210,180,.18),transparent 70%)"></div>
  <h2>Wholesale Coffee &amp; Tea for Cafés,<br>Hotels &amp; Offices</h2>
  <div class="rule" style="top:193px;background:var(--white)"></div>
  <div class="btn btn-light" style="left:494px;top:225px;width:212px;height:36px">Wholesale Solutions</div>
</section>

<!-- MEMBERSHIP -->
<section class="membership">
  <h2>The Husk &amp;<br>Kettle Membership</h2>
  <div class="rule" style="left:142px;top:209px"></div>
  <div class="subhead">Membership Benefits</div>
  <ul class="benefits">
    <li><svg width="14" height="14" viewBox="0 0 14 14"><ellipse cx="7" cy="7" rx="5" ry="6.5" transform="rotate(35 7 7)" fill="var(--rust)"/></svg>Custom French Press Travel Mug (Year One Gift)</li>
    <li><svg width="14" height="14" viewBox="0 0 14 14"><ellipse cx="7" cy="7" rx="5" ry="6.5" transform="rotate(35 7 7)" fill="var(--rust)"/></svg>Monthly coffee or tea samples</li>
    <li><svg width="14" height="14" viewBox="0 0 14 14"><ellipse cx="7" cy="7" rx="5" ry="6.5" transform="rotate(35 7 7)" fill="var(--rust)"/></svg>Expanded blend customization</li>
    <li><svg width="14" height="14" viewBox="0 0 14 14"><ellipse cx="7" cy="7" rx="5" ry="6.5" transform="rotate(35 7 7)" fill="var(--rust)"/></svg>Early access to reserve and seasonal releases</li>
  </ul>
  <div class="price">$129 First Year | $99 Annual Renewal</div>
  <div class="btn btn-dark" style="left:143px;top:453px;width:190px;height:38px">Become a Member</div>
  <div class="ph" role="img" aria-label="Friends toasting with lattes around a café table, seen from above" style="left:636px;top:106px;width:420px;height:386px;border-radius:16px;background:linear-gradient(135deg,#3a2a20,#7a5a42 40%,#c9a27a 60%,#4a3326)"></div>
</section>

<!-- TESTIMONIALS -->
<div class="section-title" style="top:3648px">Testimonials</div>
<div class="rule" style="top:3712px"></div>
<div class="quote-card" style="left:143px;top:3725px">
  <div class="stars">★★★★★</div>
  <p>Lorem ipsum dolor sit amet,consec tetur adipiscing elit, sed do eiusm od tempor incididunt ut labore et dolore magna aliqua. Ut enim ad minim veniam, quis</p>
  <hr><div class="who">John Doe</div><div class="co">Company name</div>
</div>
<div class="quote-card" style="left:456px;top:3757px">
  <div class="stars">★★★★★</div>
  <p>Lorem ipsum dolor sit amet,consec tetur adipiscing elit, sed do eiusm od tempor incididunt ut labore et dolore magna aliqua. Ut enim ad minim veniam, quis</p>
  <hr><div class="who">John Doe</div><div class="co">Company name</div>
</div>
<div class="quote-card" style="left:770px;top:3725px">
  <div class="stars">★★★★★</div>
  <p>Lorem ipsum dolor sit amet,consec tetur adipiscing elit, sed do eiusm od tempor incididunt ut labore et dolore magna aliqua. Ut enim ad minim veniam, quis</p>
  <hr><div class="who">John Doe</div><div class="co">Company name</div>
</div>
<div class="ph" role="img" aria-label="Scattered roasted coffee beans" style="left:930px;top:3955px;width:220px;height:100px;background:radial-gradient(ellipse at 50% 50%,rgba(80,40,20,.45),transparent 70%)"></div>
<div class="dots"><span></span><span class="on"></span><span></span><span></span></div>

<!-- FOOTER -->
<footer class="footer">
  <svg class="abs" style="left:0;top:0" width="1200" height="567" viewBox="0 0 1200 567">
    <path d="M0 28 C110 10 170 40 250 40 C330 40 380 -10 460 12 C540 34 560 110 640 118 C720 126 760 30 860 22 C960 14 1000 70 1080 80 C1140 88 1170 60 1200 48 L1200 567 L0 567Z" fill="var(--rust)"/>
    <path d="M0 44 C110 26 170 56 250 56 C330 56 380 6 460 28 C540 50 560 126 640 134 C720 142 760 46 860 38 C960 30 1000 86 1080 96 C1140 104 1170 76 1200 64 L1200 567 L0 567Z" fill="var(--espresso)"/>
  </svg>
  <div class="abs" role="img" aria-label="Faint coffee beans in the footer background" style="left:0;top:380px;width:1200px;height:187px;background:radial-gradient(ellipse 220px 90px at 200px 120px,rgba(20,10,5,.35),transparent 70%),radial-gradient(ellipse 260px 80px at 820px 140px,rgba(20,10,5,.3),transparent 70%)"></div>

  <div class="brand" style="left:143px;top:325px;font-size:21px">
    <span class="mark" style="width:16px;height:16px"></span>Husk and Kettle
  </div>
  <div class="social" style="left:143px" aria-label="Social link 1"></div>
  <div class="social" style="left:183px;background:var(--rust)" aria-label="Social link 2"></div>
  <div class="social" style="left:223px" aria-label="Social link 3"></div>

  <h4 style="left:392px">QUICK LINKS</h4>
  <ul class="links">
    <li>Home</li><li>About us</li><li>Products</li><li>Blog</li><li>Reviews</li><li>FAQ</li><li>Contact us</li>
  </ul>

  <h4 style="left:585px">CONTACT US</h4>
  <div class="contact-item" style="top:278px">
    <svg width="12" height="14" viewBox="0 0 12 14"><path d="M6 1a4.5 4.5 0 0 0-4.5 4.5C1.5 9 6 13 6 13s4.5-4 4.5-7.5A4.5 4.5 0 0 0 6 1z" fill="var(--rust)"/><circle cx="6" cy="5.5" r="1.6" fill="var(--espresso)"/></svg>
    <div><b>Address :</b>12, Ember Lane</div>
  </div>
  <div class="contact-item" style="top:346px">
    <svg width="13" height="13" viewBox="0 0 13 13"><path d="M3 1l2 3-1.4 1.4a8 8 0 0 0 4 4L9 8l3 2-1 2C6 12 1 7 1 2z" fill="var(--rust)"/></svg>
    <div><b>Phone :</b>+1 555 010 2468</div>
  </div>
  <div class="contact-item" style="top:412px">
    <svg width="14" height="11" viewBox="0 0 14 11"><rect x="0" y="0" width="14" height="11" rx="1.5" fill="var(--rust)"/><path d="M1 1.5 7 6l6-4.5" stroke="var(--espresso)" stroke-width="1.3" fill="none"/></svg>
    <div><b>Email Address :</b>hello@huskandkettle.test</div>
  </div>

  <h4 style="left:813px">OUR NEWSLETTER</h4>
  <div class="email-field"><svg width="14" height="11" viewBox="0 0 14 11"><rect width="14" height="11" rx="1.5" fill="#f0e6df"/><path d="M1 1.5 7 6l6-4.5" stroke="#55362a" stroke-width="1.3" fill="none"/></svg>Email address</div>
  <div class="btn btn-rust" style="left:813px;top:324px;width:126px;height:36px">Subscribe</div>
</footer>
<div class="copyright">© Copyrights 2026 | All Rights Reserved</div>

</body>
</html>
```